Business Card Design

We need a business card designed for our new company. Prefer a black card with white logo & writing.

Contact Information for Business Card

Ted Galloway, address: 7-4812 Fernhollow Road, Abbotsford, BC, V3K 8R2, Office Phone: 604-712-3390, Cell: 604-947-2164, Email: ted@resinworkshub.ca

Colors

Designer to choose only greyscale colors for use in the design.

```html
<!DOCTYPE html>
<html lang="en">
<head>
<meta charset="utf-8">
<title>Resinworks Hub – Business Card</title>
<link rel="stylesheet" href="https://fonts.googleapis.com/css2?family=Montserrat:wght@400;700&display=swap">
<style>
  :root {
    --backdrop: #9b9b9b;
    --card: #212121;
    --ink: #ffffff;
    --ink-soft: #e6e6e6;
  }
  * { margin: 0; padding: 0; box-sizing: border-box; }
  html, body {
    width: 1093px; height: 1200px; overflow: hidden;
    background: var(--backdrop);
    font-family: "Montserrat", sans-serif;
    color: var(--ink);
  }
  .card {
    position: absolute;
    left: 265px;
    width: 581px;
    height: 365px;
    background: var(--card);
    border-radius: 18px;
  }
  .card--front { top: 225px; }
  .card--back { top: 616px; }

  .holder { position: absolute; left: 28px; top: 38px; }
  .holder__name { font-weight: 700; font-size: 21px; letter-spacing: 0.2px; line-height: 1; }
  .holder__role { font-weight: 400; font-size: 13px; color: var(--ink-soft); margin-top: 8px; }

  .brand {
    position: absolute;
    font-weight: 700;
    color: var(--ink);
    text-transform: uppercase;
    text-align: center;
    line-height: 1.05;
  }
  .brand--front { left: 360px; top: 40px; width: 170px; font-size: 22px; top: 52px; }
  .brand--back { left: 0; width: 100%; top: 128px; font-size: 50px; letter-spacing: 1px; }

  .contacts { position: absolute; left: 27px; top: 256px; list-style: none; }
  .contacts li {
    display: flex; align-items: center;
    height: 22px; font-size: 13px; font-weight: 400;
    margin-bottom: 0;
  }
  .contacts li:nth-child(1) { height: 24px; }
  .contacts li:nth-child(2) { height: 24px; }
  .contacts svg { width: 13px; height: 13px; margin-right: 9px; fill: var(--ink); flex: none; }

  .address {
    position: absolute; left: 369px; top: 305px;
    font-size: 13px; font-weight: 400; line-height: 16px;
    font-style: normal;
  }
</style>
</head>
<body>
  <section class="card card--front">
    <div class="holder">
      <div class="holder__name">Ted Galloway</div>
      <div class="holder__role">owner</div>
    </div>

    <div class="brand brand--front">Resinworks<br>Hub</div>

    <ul class="contacts">
      <li>
        <svg viewBox="0 0 16 16" aria-hidden="true"><path d="M3.6 1.2l2.3 2.6-1.3 1.8c.9 2 2.5 3.6 4.5 4.5l1.8-1.3 2.6 2.3-1.2 2.2C7.4 15 1 8.6 1.2 3.5z"/></svg>
        604-712-3390
      </li>
      <li>
        <svg viewBox="0 0 16 16" aria-hidden="true"><path d="M4.5 0.5h7a1 1 0 0 1 1 1v13a1 1 0 0 1-1 1h-7a1 1 0 0 1-1-1v-13a1 1 0 0 1 1-1zm.7 2v9.5h5.6V2.5zM8 12.8a.9.9 0 1 0 0 1.8.9.9 0 0 0 0-1.8z"/></svg>
        604-947-2164
      </li>
      <li>
        <svg viewBox="0 0 16 16" aria-hidden="true"><path d="M1 3.5h14v1L8 9 1 4.5zM1 6.2l7 4.4 7-4.4V13H1z"/></svg>
        ted@resinworkshub.ca
      </li>
      <li>
        <svg viewBox="0 0 16 16" aria-hidden="true"><path d="M8 .8a7.2 7.2 0 1 0 0 14.4A7.2 7.2 0 0 0 8 .8zm-1 2c.6.7.4 1.6-.5 2.1-.9.4-.9 1.4 0 1.9.8.5.5 1.5-.3 1.7-1 .3-1.5 1.2-1 2.3.3.7-.2 1.4-1 1.3A5.6 5.6 0 0 1 7 2.8zm3.6 1.3a5.6 5.6 0 0 1 1.1 8c-.5-.6-.4-1.4.2-2 .5-.6.1-1.5-.7-1.5-.9 0-1.3-.8-.8-1.5.4-.6.1-1.3-.5-1.5-.5-.2-.4-1 .1-1.2z"/></svg>
        www.resinworkshub.ca
      </li>
    </ul>

    <address class="address">
      7-4812 Fernhollow Road,<br>
      Abbotsford, BC, V3K 8R2
    </address>
  </section>

  <section class="card card--back">
    <div class="brand brand--back">Resinworks<br>Hub</div>
  </section>
</body>
</html>
```